Classy, Elegant, Simple Business Card Design

Looking to have a classy, simple, and elegant design. Want a top notch designed business card. I really like the look of the new torvane credit card. I also like the design I attached. I am trying to reach 21-29 year old females for booking us for there wedding or event. We offer Disc Jockey Service, Photo Booth Rentals, and Uplighting .

Target Market(s)

21-28 year old females

Contact Information for Business Card

Has to have logo, website, email, and phone number

Font styles to use
Other font styles liked:
• open to font choice, modern, clean
Designer to choose
33a6d7
0791cd
0555a3
ffffff

Requirements
Must have
• Has to have logo, website, email, and phone number
Nice to have
• I really like the design of the new torvane credit card. I also included my logo and some designs I like
Should not have
• clutter or too much info

```html
<!DOCTYPE html>
<html lang="en">
<head>
<meta charset="utf-8">
<title>Tidewell Event Group – Business Card</title>
<link rel="stylesheet" href="https://fonts.googleapis.com/css2?family=Questrial&display=swap">
<style>
  :root {
    --bg-top: #5a5d61;
    --bg-bottom: #2a2c2f;
    --card: #0b0c10;
    --blue-light: #33a6d7;
    --blue: #0791cd;
    --blue-deep: #0555a3;
    --white: #ffffff;
    --muted: #9aa0a6;
    --ghost: #16181d;
  }
  * { margin: 0; padding: 0; box-sizing: border-box; }
  html, body {
    width: 1200px;
    height: 900px;
    overflow: hidden;
  }
  body {
    background: linear-gradient(160deg, var(--bg-top), var(--bg-bottom));
    font-family: "Questrial", "Century Gothic", sans-serif;
    display: flex;
    flex-direction: column;
    align-items: center;
    justify-content: center;
    gap: 40px;
  }
  .card {
    position: relative;
    width: 700px;
    height: 400px;
    background: var(--card);
    border-radius: 36px;
    box-shadow: 0 18px 40px rgba(0, 0, 0, 0.45);
    overflow: hidden;
  }
  .brand {
    display: flex;
    align-items: center;
    gap: 14px;
    color: var(--blue);
    font-size: 34px;
    letter-spacing: 3px;
    white-space: nowrap;
  }
  .brand-dot {
    width: 18px;
    height: 18px;
    border-radius: 50%;
    background: var(--blue);
    flex: none;
  }
  .card-front .brand {
    position: absolute;
    left: 50%;
    top: 50%;
    transform: translate(-50%, -50%);
  }
  .card-back .brand {
    position: absolute;
    right: 60px;
    top: 70px;
    font-size: 22px;
    letter-spacing: 2px;
    gap: 10px;
  }
  .card-back .brand-dot { width: 12px; height: 12px; }
  .ghost-name {
    position: absolute;
    left: 40px;
    bottom: 40px;
    font-size: 96px;
    color: var(--ghost);
    letter-spacing: 2px;
    line-height: 1;
  }
  .contact {
    position: absolute;
    right: 60px;
    top: 200px;
    list-style: none;
    display: flex;
    flex-direction: column;
    gap: 16px;
  }
  .contact-item {
    display: flex;
    align-items: center;
    gap: 12px;
    color: var(--white);
    font-size: 19px;
  }
  .contact-icon {
    width: 16px;
    height: 16px;
    flex: none;
  }
</style>
</head>
<body>

  <section class="card card-front" aria-label="Card front">
    <div class="brand"><span class="brand-dot"></span>TIDEWELL EVENT GROUP</div>
  </section>

  <section class="card card-back" aria-label="Card back">
    <div class="ghost-name" aria-hidden="true">Tidewell</div>
    <div class="brand"><span class="brand-dot"></span>TIDEWELL EVENT GROUP</div>
    <ul class="contact">
      <li class="contact-item">
        <svg class="contact-icon" viewBox="0 0 16 16" aria-hidden="true">
          <path d="M3 1.5l3 .5 1 3-1.6 1.3a9 9 0 0 0 4.3 4.3L11 9l3 1 .5 3-1.5 1.5C7 14.5 1.5 9 1.5 3z" fill="var(--blue)"/>
        </svg>
        +1 555 014 2290
      </li>
      <li class="contact-item">
        <svg class="contact-icon" viewBox="0 0 16 16" aria-hidden="true">
          <rect x="1" y="3" width="14" height="10" rx="1" fill="var(--blue)"/>
          <path d="M1.5 3.8L8 9l6.5-5.2" fill="none" stroke="var(--card)" stroke-width="1.4"/>
        </svg>
        info@tidewellevents.com
      </li>
      <li class="contact-item">
        <svg class="contact-icon" viewBox="0 0 16 16" aria-hidden="true">
          <circle cx="8" cy="8" r="7" fill="var(--blue)"/>
          <path d="M1 8h14M8 1c-3 3.5-3 10.5 0 14M8 1c3 3.5 3 10.5 0 14" fill="none" stroke="var(--card)" stroke-width="1"/>
        </svg>
        www.tidewellevents.com
      </li>
    </ul>
  </section>

</body>
</html>
```